Social responsible Renewable Energy company

We at brivoX are an independent power producer company founded in 2021 that handles large scale deployment of Renewable Energy and carbon neutral Energy as a service model. We offer turnkey solutions using solar panel systems and this could be incorporated in our business cards. You can also find our logo in the documents provided. Another key issue is that the business cards will be printed on recicled paper, not sure if this is a limitation in deciding the design. The recycled sign should also be added on the business card and stating that the paper used was recycled. Our website is www.mybrivox-example.com. It should also be very professional, not too dreamy but still needs to capture your imagination. We are really excited to get your ideas !

Target Market(s)

Renewable Energy market

Contact Information for Business Card

The business card will be printed on recycled paper. Name of the company is brivoX. Website is www.mybrivox-example.com

Requirements
Nice to have
• Our motto: Powered by renewable, driven by people.

```html
<!DOCTYPE html>
<html lang="en">
<head>
<meta charset="utf-8">
<title>brivoX business card</title>
<link href="https://fonts.googleapis.com/css2?family=Manrope:wght@400;500;700&display=swap" rel="stylesheet">
<style>
  :root {
    --backdrop: #c9cbce;
    --kraft: #d9d0c1;
    --navy: #163754;
    --green: #2f8f2a;
    --ink-light: #e8e4dc;
    --muted: #8f877a;
  }
  html, body {
    margin: 0;
    width: 1200px;
    height: 857px;
    overflow: hidden;
    background: var(--backdrop);
    font-family: "Manrope", sans-serif;
  }
  .canvas {
    position: relative;
    width: 1200px;
    height: 857px;
  }
  .card {
    position: absolute;
    top: 274px;
    width: 540px;
    height: 309px;
    background: var(--kraft);
    overflow: hidden;
    box-shadow: 0 6px 18px rgba(0,0,0,0.18);
  }
  .card--front { left: 40px; }
  .card--back { left: 620px; }
  .card svg.shapes {
    position: absolute;
    inset: 0;
  }
  .brand-name {
    position: absolute;
    margin: 0;
    color: var(--navy);
    font-weight: 700;
    letter-spacing: 1px;
    line-height: 1;
  }
  .card--front .brand-name {
    top: 62px;
    left: 0;
    width: 100%;
    text-align: center;
    font-size: 78px;
  }
  .card--back .brand-name {
    top: 24px;
    right: 34px;
    font-size: 44px;
  }
  .solar-field {
    position: absolute;
    left: 0;
    bottom: 0;
    width: 100%;
    height: 118px;
    background: linear-gradient(180deg, #1b3f60 0%, var(--navy) 100%);
  }
  .recycled {
    position: absolute;
    top: 30px;
    left: 188px;
    display: flex;
    align-items: center;
    gap: 6px;
    color: var(--muted);
    font-size: 8px;
    text-transform: uppercase;
    letter-spacing: 0.5px;
  }
  .recycled-badge {
    width: 22px;
    height: 22px;
    border: 1.2px solid var(--muted);
    border-radius: 50%;
  }
  .person {
    position: absolute;
    top: 128px;
    left: 30px;
    color: var(--ink-light);
  }
  .person-name {
    margin: 0;
    font-size: 20px;
    font-weight: 700;
    color: var(--kraft);
  }
  .person-title {
    margin: 4px 0 0;
    font-size: 10px;
    letter-spacing: 0.6px;
    color: #b9b3a8;
  }
  .contact-list {
    list-style: none;
    margin: 20px 0 0;
    padding: 0;
    font-size: 11.5px;
    line-height: 17px;
  }
  .contact-list li {
    display: flex;
    align-items: center;
    gap: 9px;
  }
  .contact-list svg { width: 10px; height: 10px; fill: var(--ink-light); }
  .company-address {
    position: absolute;
    top: 128px;
    left: 330px;
    margin: 0;
    font-style: normal;
    font-size: 11.5px;
    line-height: 16px;
    color: var(--ink-light);
  }
  .company-address strong { font-weight: 700; }
</style>
</head>
<body>
<main class="canvas">

  <section class="card card--front" aria-label="Business card front">
    <h1 class="brand-name">brivoX</h1>
    <div class="solar-field" role="img" aria-label="Solar panel cell grid pattern in navy"></div>
  </section>

  <section class="card card--back" aria-label="Business card back">
    <svg class="shapes" width="540" height="309" viewBox="0 0 540 309" aria-hidden="true">
      <polygon points="250,96 540,96 540,88 258,88" fill="var(--green)"/>
      <polygon points="0,112 236,112 250,96 540,96 540,262 0,262" fill="var(--navy)"/>
      <polygon points="0,262 270,262 262,272 0,272" fill="var(--green)"/>
    </svg>

    <h2 class="brand-name">brivoX</h2>

    <div class="recycled">
      <span class="recycled-badge" aria-hidden="true"></span>
      <span>Recycled paper</span>
    </div>

    <div class="person">
      <p class="person-name">Daniel Harlow</p>
      <p class="person-title">DIRECTOR</p>
      <ul class="contact-list">
        <li>
          <svg viewBox="0 0 10 10" aria-hidden="true"><path d="M2 0.5 L3.6 2.6 L2.8 3.6 Q4 6 6.4 7.2 L7.4 6.4 L9.5 8 L8.4 9.5 Q3.5 9 0.5 1.6 Z"/></svg>
          (555) 010 2040
        </li>
        <li>
          <svg viewBox="0 0 10 10" aria-hidden="true"><path d="M0.5 2 H9.5 V8 H0.5 Z M1 2.4 L5 5.4 L9 2.4" stroke="#163754" stroke-width="0.8"/></svg>
          info@mybrivox-example.com
        </li>
        <li>
          <svg viewBox="0 0 10 10" aria-hidden="true"><circle cx="5" cy="5" r="4.5"/></svg>
          www.mybrivox-example.com
        </li>
      </ul>
    </div>

    <address class="company-address">
      <strong>Brivo X</strong><br>
      4512 Harbor Lane<br>
      Eastfield, XL 40917
    </address>
  </section>

</main>
</body>
</html>
```